Construction Company

Design a clutter free business card, it can be double-sided utilizing the logo for VKM Ltd simple with all relevant contact information.

Please also a letterhead design to function for the purposes of invoicing, all mail requirements, with header to be distinctive while the footer ties page together and incorporates all necessary information.

For now, please use generic / dummy text and when a winner is selected, I will disclose the contact information.

Hi Designers! Please read the updated brief which includes the design of a business card and letterhead. Thank you!

```html
<!DOCTYPE html>
<html lang="en">
<head>
<meta charset="utf-8">
<title>VKM Ltd – Business Card</title>
<link rel="stylesheet" href="https://fonts.googleapis.com/css2?family=Arimo:wght@400;700&display=swap">
<style>
  :root {
    --page-bg: #e6e2e0;
    --card-bg: #f5f3f3;
    --brand-blue: #023496;
    --brand-gold: #b89a1e;
    --text-light: #ffffff;
  }
  * { margin: 0; padding: 0; box-sizing: border-box; }
  html, body {
    width: 1200px;
    height: 900px;
    overflow: hidden;
    background: var(--page-bg);
    font-family: "Arimo", Arial, sans-serif;
  }
  .business-card {
    position: absolute;
    left: 100px;
    top: 141px;
    width: 1000px;
    height: 618px;
    background: var(--card-bg);
    overflow: hidden;
    box-shadow: 0 10px 30px rgba(0, 0, 0, 0.12);
  }
  .card-panel {
    position: absolute;
    inset: 0;
    width: 100%;
    height: 100%;
  }
  .contact-block {
    position: absolute;
    left: 38px;
    top: 120px;
    color: var(--text-light);
  }
  .person-name {
    font-weight: 700;
    font-size: 33px;
    line-height: 1.1;
    letter-spacing: 0.2px;
  }
  .person-title {
    font-size: 28px;
    line-height: 1.2;
    margin-top: 2px;
  }
  .contact-list {
    list-style: none;
    margin-top: 24px;
  }
  .contact-item {
    display: flex;
    align-items: center;
    font-size: 27px;
    line-height: 36px;
    white-space: nowrap;
  }
  .contact-icon {
    width: 26px;
    height: 26px;
    margin-right: 12px;
    flex: none;
  }
  .postal-address {
    font-style: normal;
    font-size: 27px;
    line-height: 36px;
    margin-top: 18px;
    white-space: nowrap;
  }
  .company-name {
    position: absolute;
    left: 584px;
    top: 432px;
    font-size: 84px;
    font-weight: 700;
    color: var(--brand-blue);
    letter-spacing: 1px;
    white-space: nowrap;
  }
</style>
</head>
<body>
  <section class="business-card">
    <svg class="card-panel" viewBox="0 0 1000 618" preserveAspectRatio="none" aria-hidden="true">
      <path d="M0 0 H320 C520 120 640 230 640 309 C640 388 520 498 320 618 H0 Z" fill="var(--brand-gold)" transform="translate(8 0)"/>
      <path d="M0 0 H320 C520 120 640 230 640 309 C640 388 520 498 320 618 H0 Z" fill="var(--brand-blue)"/>
    </svg>

    <div class="contact-block">
      <h1 class="person-name">MARCUS BELLAMY</h1>
      <p class="person-title">Managing Director</p>
      <ul class="contact-list">
        <li class="contact-item">
          <svg class="contact-icon" viewBox="0 0 24 24" fill="none" stroke="currentColor" stroke-width="2" aria-hidden="true"><path d="M5 3h4l2 5-2.5 1.5a11 11 0 0 0 6 6L16 13l5 2v4a2 2 0 0 1-2 2A16 16 0 0 1 3 5a2 2 0 0 1 2-2z"/></svg>
          021-555 018 274
        </li>
        <li class="contact-item">
          <svg class="contact-icon" viewBox="0 0 24 24" fill="none" stroke="currentColor" stroke-width="2" aria-hidden="true"><rect x="6" y="2" width="12" height="20" rx="2"/><circle cx="12" cy="18" r="1" fill="currentColor"/></svg>
          021-555 018 275
        </li>
        <li class="contact-item">
          <svg class="contact-icon" viewBox="0 0 24 24" fill="currentColor" aria-hidden="true"><path d="M2 5h20v14H2z M3 6l9 7 9-7" stroke="var(--brand-blue)" stroke-width="1.5"/></svg>
          hello@vkmbuild.com
        </li>
        <li class="contact-item">
          <svg class="contact-icon" viewBox="0 0 24 24" fill="none" stroke="currentColor" stroke-width="1.8" aria-hidden="true"><circle cx="12" cy="12" r="10"/><ellipse cx="12" cy="12" rx="4.5" ry="10"/><path d="M2 12h20M4 7h16M4 17h16"/></svg>
          www.vkmbuild.com
        </li>
      </ul>
      <address class="postal-address">58, Kestrel Road, Suite 4<br>Dunmore 30418, Valeland</address>
    </div>

    <p class="company-name">VKM Ltd</p>
  </section>
</body>
</html>
```